Law Firm Website

We are a small California based law firm specializing in business, corporate and litigation matters. We need to have our website redesigned. We are looking for a new and fresh look for our site, keeping in mind that we are a law firm.
What we don't want:
**the traditional "gavel" and "scales of justice" look
**anything too crazy
What we do want:
**sophisticated yet modern and fresh corporate look and feel
**samples of websites we really like:
http://www.tarnwellhope.example
http://www.marrowgate.example/
we also like:
http://www.fenwoodastley.example/
http://www.qz.example/
http://www.brenhollow.example/
http://www.pvdn.example
http://www.nqrlaw.example/
The content will be whatever is currently on our website (www.okabelawgroup.example). We will be selecting the winner based on originality and keeping the above requirements in mind. Please note that the photos that you use will be the ones that we will be using, so choose wisely because the photos will make a difference.
Target Market(s)
Corporate clients
Industry/Entity Type
Law Firm
Look and feel

```html
<!DOCTYPE html>
<html lang="en">
<head>
<meta charset="utf-8">
<title>Okabe Law Group, LLP – Law Center</title>
<link href="https://fonts.googleapis.com/css2?family=Arimo:wght@400&family=Oswald:wght@500;600&family=Roboto+Condensed:wght@300;400;700&display=swap" rel="stylesheet">
<style>
  :root {
    --ink: #000000;
    --paper: #ffffff;
    --body-text: #2b2b2b;
    --rule: #bdbdbd;
    --footer-bg: #000000;
    --footer-head: #bcbcbc;
    --footer-link: #a8a8a8;
    --brand-blue-light: #8cc4f2;
    --brand-blue: #2a86d8;
    --brand-blue-deep: #0f5fae;
    --hero-sky: #f3f3f3;
    --hero-city: #dcdcdc;
    --hero-team: rgba(45, 45, 45, 0.62);
    --hero-team-edge: rgba(110, 110, 110, 0.28);
  }
  * { box-sizing: border-box; margin: 0; padding: 0; }
  html, body { width: 1189px; height: 1200px; overflow: hidden; background: var(--paper); }
  .page { position: relative; width: 1189px; height: 1200px; overflow: hidden; font-family: "Roboto Condensed", sans-serif; color: var(--ink); }

  .top-bar { position: absolute; left: 0; top: 0; width: 100%; height: 7px; background: var(--ink); }
  .phone-tab { position: absolute; left: 962px; top: 0; width: 173px; height: 53px; background: var(--ink); border-radius: 0 0 10px 10px; display: flex; align-items: center; justify-content: center; gap: 10px; color: var(--paper); font-weight: 700; font-size: 17px; padding-top: 6px; }
  .phone-tab svg { width: 22px; height: 24px; }

  .brand { position: absolute; left: 30px; top: 46px; }
  .brand-mark { position: absolute; left: 56px; top: 0; width: 115px; height: 116px; background: linear-gradient(100deg, var(--brand-blue-light) 0%, var(--brand-blue) 45%, var(--brand-blue-deep) 100%); }
  .brand-name { position: absolute; left: 0; top: 118px; white-space: nowrap; font-family: "Oswald", sans-serif; font-weight: 600; font-size: 26px; color: var(--ink); line-height: 1.3; }

  .main-nav { position: absolute; left: 369px; top: 105px; width: 820px; height: 28px; border-bottom: 1px solid var(--rule); }
  .main-nav a { position: absolute; top: 0; font-weight: 700; font-size: 16px; color: var(--ink); text-decoration: none; letter-spacing: 0.2px; }
  .main-nav .sep { position: absolute; top: 15px; width: 1px; height: 12px; background: var(--rule); }

  .hero-title { position: absolute; left: 25px; top: 388px; font-family: "Arimo", sans-serif; font-weight: 400; font-size: 61px; letter-spacing: 0.5px; line-height: 1; }
  .hero-copy { position: absolute; left: 27px; top: 466px; width: 372px; height: 270px; overflow: hidden; font-size: 14px; line-height: 27.3px; text-align: justify; color: var(--body-text); }
  .scroll-track { position: absolute; left: 415px; top: 473px; width: 24px; height: 261px; border: 1px solid var(--rule); border-radius: 12px; }
  .scroll-track .thumb { position: absolute; left: 8px; top: 85px; width: 7px; height: 92px; background: var(--ink); border-radius: 4px; }
  .scroll-track svg { position: absolute; left: 6px; width: 10px; height: 8px; }

  .cta { position: absolute; left: 27px; top: 791px; width: 369px; height: 54px; background: var(--ink); color: var(--paper); display: flex; align-items: center; justify-content: center; font-size: 20px; font-weight: 400; text-decoration: none; letter-spacing: 0.2px; }

  .hero-photo {
    position: absolute; left: 458px; top: 270px; width: 660px; height: 580px;
    background:
      radial-gradient(ellipse 34% 40% at 52% 60%, var(--hero-team) 0%, var(--hero-team-edge) 60%, rgba(255,255,255,0) 100%),
      linear-gradient(to bottom, var(--paper) 0%, var(--hero-sky) 20%, var(--hero-city) 55%, var(--hero-sky) 80%, var(--paper) 100%);
    -webkit-mask-image: radial-gradient(ellipse 50% 50% at 50% 50%, #000 55%, transparent 100%);
    mask-image: radial-gradient(ellipse 50% 50% at 50% 50%, #000 55%, transparent 100%);
  }

  .site-footer { position: absolute; left: 0; top: 982px; width: 100%; height: 218px; background: var(--footer-bg); }
  .footer-col { position: absolute; top: 38px; }
  .footer-col h3 { font-weight: 300; font-size: 20px; color: var(--footer-head); letter-spacing: 0.3px; margin-bottom: 9px; }
  .footer-col ul { list-style: none; }
  .footer-col li { font-size: 14px; color: var(--footer-link); line-height: 27.4px; }
  .footer-col li::before { content: "// "; }
  .footer-links { left: 27px; }
  .footer-social { left: 426px; }
  .footer-contact { position: absolute; left: 825px; top: 38px; color: var(--footer-link); font-family: "Arimo", sans-serif; font-size: 14px; line-height: 18px; }
  .footer-contact h2 { font-family: "Oswald", sans-serif; font-weight: 500; font-size: 39px; color: var(--paper); line-height: 1; margin-bottom: 2px; }
  .footer-contact .copyright { margin-top: 35px; font-size: 15px; }
</style>
</head>
<body>
<div class="page">
  <div class="top-bar"></div>
  <div class="phone-tab">
    <svg viewBox="0 0 22 24" aria-hidden="true"><circle cx="11" cy="6" r="5" fill="#fff"/><path d="M1 24 C1 15 6 13 11 13 C16 13 21 15 21 24 Z" fill="#fff"/></svg>
    <span>000-000-000</span>
  </div>

  <div class="brand">
    <div class="brand-mark"></div>
    <div class="brand-name">Okabe Law Group, LLP</div>
  </div>

  <nav class="main-nav">
    <a href="#" style="left:274px">HOME</a>
    <span class="sep" style="left:342px"></span>
    <a href="#" style="left:379px">ABOUT US</a>
    <span class="sep" style="left:482px"></span>
    <a href="#" style="left:521px">SERVICES</a>
    <span class="sep" style="left:624px"></span>
    <a href="#" style="left:652px">CONTACT US</a>
  </nav>

  <h1 class="hero-title">LAW CENTER</h1>
  <p class="hero-copy">Lorem Ipsum is simply dummy text of the printing and typesetting industry. Lorem Ipsum has been the industry's standard dummy text ever since the 1500s, when an unknown printer took a galley of type and scrambled it to make a type specimen book. It has survived not only five centuries, but also the leap lishing software like Quillset Composer including versions of Lorem Ipsum.Lorem Ipsum is simply dummy text of the printing and te 1500sLorem Ipsum is simply dummy text of the printing and typesetting industry. Lorem Ipsum has been the industry's standard dummy text ever since the 1500s, when an unknown printer took a galley</p>
  <div class="scroll-track">
    <svg style="top:7px" viewBox="0 0 10 8" aria-hidden="true"><path d="M5 0 L10 8 L0 8 Z" fill="#000"/></svg>
    <div class="thumb"></div>
    <svg style="bottom:7px" viewBox="0 0 10 8" aria-hidden="true"><path d="M0 0 L10 0 L5 8 Z" fill="#000"/></svg>
  </div>
  <a class="cta" href="#">CONTACT US FOR QUICK ADVICE</a>

  <div class="hero-photo" role="img" aria-label="Black and white photo of a team of lawyers in business suits standing in front of city skyscrapers"></div>

  <footer class="site-footer">
    <div class="footer-col footer-links">
      <h3>QUICK LINKS</h3>
      <ul><li>Home</li><li>Services</li><li>Contact us</li><li>Privacy policy</li></ul>
    </div>
    <div class="footer-col footer-social">
      <h3>SOCIAL</h3>
      <ul><li>Friendwall</li><li>Chirper</li><li>Worklink</li><li>Blog</li></ul>
    </div>
    <div class="footer-contact">
      <h2>LAW CENTER</h2>
      <p>417 Larchmere Row, Suite 300 Brindlecove, WA 98000</p>
      <p>P.O Brindlecove //&nbsp; Phone: 000-000-000</p>
      <p class="copyright">Copyright 2014 lawcenter.example</p>
    </div>
  </footer>
</div>
</body>
</html>
```